Diverse, up-scale salon needs eye-catching, unique business cards.

We are looking for a unique business card design for our stylist but that can also be multi functional and used for appointment reminder and referrals. I will need a design in a format that I can modify names and titles going forward. In the past we have had a dark background with the logo on one side, and stylist and contact information on the other but we are open to all ideas. I have included our mission statement as well as branded colors below. The statement doesn't need to go on the card, it's just a reference for target market. We need space for the stylists name, title, instagram handle and then the salons phone number, website and address. I am also open to adding a spot for a qr code linked to the stylist instagram or the salon booking link.

primary brand colors:
#333333 #233415 #36502a #93874a #000000
Mission statement:
Vessolin Hair Studio, a high-end salon located in the lively Downtown Farmington, Michigan, is committed to providing exceptional services in a welcoming and relaxed environment to meet the needs of our diverse clientele.
Our salon specializes in contemporary custom haircuts, coloring, extensions, and barbering and beard grooming services. Our team of skilled stylists is passionate and inventive in their hair styling techniques. At the heart of our salon are values centered on quality, innovation, creativity, and above all, comfort. These core values are evident in every appointment across our customizable array of services.
Our goal is to establish a benchmark for exceptional hair care for every human.
Website: www.vessolinhairstudio.example
instagram: @vessolinhairstudio
address: 41782 Pelham Crest Rd, Larkmoor Heights
phone: 555-555-0147

Industry/Entity Type

Hair Salon

Contact Information for Business Card

Stylist name, title, phone, instagram, website, address, (optional qr code)

Requirements
Should not have
• Does not need mission statement on the card.

```html
<!DOCTYPE html>
<html lang="en">
<head>
<meta charset="utf-8">
<title>Vessolin Hair Studio – Business Card</title>
<link rel="stylesheet" href="https://fonts.googleapis.com/css2?family=Poppins:wght@400;700&family=Oswald:wght@600&display=swap">
<style>
  :root {
    --page: #ffffff;
    --black: #000000;
    --charcoal: #222222;
    --gold: #93874a;
    --gold-light: #aca066;
    --gold-deep: #978a57;
    --white: #ffffff;
  }
  * { box-sizing: border-box; margin: 0; padding: 0; }
  html, body { width: 1200px; height: 1200px; overflow: hidden; background: var(--page); }
  .card {
    position: absolute; left: 196px; width: 818px; height: 467px; overflow: hidden;
  }
  /* Front */
  .card-front { top: 101px; background: radial-gradient(ellipse at 50% 95%, #141414 0%, var(--black) 70%); }
  .wave-area { position: absolute; left: 0; width: 100%; }
  .card-front .wave-area {
    top: 180px; height: 250px;
    background: linear-gradient(180deg, rgba(255,255,255,0) 0%, rgba(255,255,255,0.06) 50%, rgba(255,255,255,0) 100%);
  }
  .emblem {
    position: absolute; width: 176px; height: 176px; border-radius: 50%;
    display: flex; align-items: center; justify-content: center; text-align: center;
  }
  .card-front .emblem { left: 316px; top: 89px; border: 3px solid var(--gold); }
  .emblem-name {
    font-family: "Oswald", sans-serif; font-weight: 600; font-size: 21px;
    letter-spacing: 2px; line-height: 1.25; text-transform: uppercase; width: 130px;
  }
  .card-front .emblem-name { color: var(--gold); }
  .url-band {
    position: absolute; left: 0; top: 351px; width: 100%; height: 23px; background: var(--gold);
  }
  .url-pill {
    position: absolute; left: 184px; top: 343px; width: 450px; height: 40px;
    background: var(--black); border-radius: 20px;
    display: flex; align-items: center; justify-content: center;
    font-family: "Poppins", sans-serif; font-size: 25px; color: var(--white); white-space: nowrap;
  }
  /* Back */
  .card-back { top: 625px; background: linear-gradient(180deg, var(--gold-light) 0%, var(--gold-light) 30%, var(--gold-deep) 100%); }
  .card-back .wave-area {
    top: 190px; height: 230px;
    background: linear-gradient(180deg, rgba(200,190,120,0) 0%, rgba(200,190,120,0.28) 55%, rgba(200,190,120,0) 100%);
  }
  .accent-bar {
    position: absolute; left: 78px; top: 0; width: 25px; height: 131px;
    background: var(--black); border-radius: 0 0 13px 13px;
  }
  .studio-title {
    position: absolute; left: 75px; top: 138px;
    font-family: "Poppins", sans-serif; font-weight: 700; font-size: 33px;
    color: var(--charcoal); letter-spacing: -0.3px; white-space: nowrap; line-height: 46px;
  }
  .studio-title .first { color: var(--white); }
  .contact-list { position: absolute; left: 75px; top: 197px; list-style: none; }
  .contact-item {
    display: flex; align-items: center; height: 26px; margin-bottom: 9px;
    font-family: "Poppins", sans-serif; font-size: 19px; color: var(--charcoal); white-space: nowrap;
  }
  .contact-icon {
    width: 26px; height: 26px; border-radius: 50%; background: var(--charcoal);
    margin-right: 8px; flex: none; display: flex; align-items: center; justify-content: center;
  }
  .card-back .emblem { left: 580px; top: 141px; border: 3px solid var(--black); }
  .card-back .emblem-name { color: var(--black); }
</style>
</head>
<body>
  <section class="card card-front">
    <div class="wave-area" role="img" aria-label="Flowing grey line waves across the card"></div>
    <div class="emblem"><span class="emblem-name">Vessolin Hair Studio</span></div>
    <div class="url-band"></div>
    <div class="url-pill">www.vessolinhairstudio.example</div>
  </section>

  <section class="card card-back">
    <div class="wave-area" role="img" aria-label="Flowing pale gold line waves across the card"></div>
    <div class="accent-bar"></div>
    <h1 class="studio-title"><span class="first">VESSOLIN</span> HAIR STUDIO</h1>
    <ul class="contact-list">
      <li class="contact-item">
        <span class="contact-icon">
          <svg width="14" height="14" viewBox="0 0 24 24"><path fill="#fff" d="M6.6 10.8a15 15 0 0 0 6.6 6.6l2.2-2.2a1 1 0 0 1 1-.25 11.4 11.4 0 0 0 3.6.57 1 1 0 0 1 1 1V20a1 1 0 0 1-1 1A17 17 0 0 1 3 4a1 1 0 0 1 1-1h3.5a1 1 0 0 1 1 1c0 1.25.2 2.45.57 3.6a1 1 0 0 1-.25 1z"/></svg>
        </span>555-555-0147
      </li>
      <li class="contact-item">
        <span class="contact-icon">
          <svg width="14" height="14" viewBox="0 0 24 24"><path fill="#fff" d="M12 2a7 7 0 0 0-7 7c0 5.2 7 13 7 13s7-7.8 7-13a7 7 0 0 0-7-7zm0 9.5A2.5 2.5 0 1 1 12 6.5a2.5 2.5 0 0 1 0 5z"/></svg>
        </span>41782 Pelham Crest Rd, Larkmoor Heights
      </li>
      <li class="contact-item">
        <span class="contact-icon"></span>@vessolinhairstudio
      </li>
      <li class="contact-item">
        <span class="contact-icon">
          <svg width="15" height="15" viewBox="0 0 24 24" fill="none" stroke="#fff" stroke-width="1.8"><circle cx="12" cy="12" r="9"/><ellipse cx="12" cy="12" rx="4" ry="9"/><path d="M3 12h18M4.5 7.5h15M4.5 16.5h15"/></svg>
        </span>www.vessolinhairstudio.example
      </li>
    </ul>
    <div class="emblem"><span class="emblem-name">Vessolin Hair Studio</span></div>
  </section>
</body>
</html>
```